New Business Card Design Project LORVANTI-Italy

we are LORVANTI-Italy
our company in the market for 3 years we are luxury cosmetic company and its about time for a facelift :)
i will like to have elegant luxurious and unique business card
that will give the person that get it a unique, luxurious and elegant impression
I'm VERY OPEN FOR NEW IDEAS , even duo i add a few files of things that i see on line and i like them

i add my logo as well
my website is LORVANTI.COM
(if you would like to see the main style that we have)

Target Market(s)

adult that have money :)

Industry/Entity Type

Business

Contact Information for Business Card

Name - Dario Lorvanti
Position - CEO and CO Founder
address - 4817 E Halvern
telephone - 555-384-1926
email - dario@lorvanti.com
fax - 555-384-1926
website - LORVANTI.COM

Colors
000000
959595
fbee3e
ffffff

Requirements
Must have
• big logo in GOLD color
• elegant look
• impressive
Nice to have
• not must but maybe classy pattern background
• not must but maybe emblem
• maybe clear plastic business card
Should not have
• colors
• images

```html
<!DOCTYPE html>
<html lang="en">
<head>
<meta charset="utf-8">
<title>LORVANTI Italy — Business Card</title>
<link rel="stylesheet" href="https://fonts.googleapis.com/css2?family=Cinzel:wght@400;600&family=PT+Sans:wght@400&display=swap">
<style>
  :root {
    --backdrop: #3b322d;
    --card-black: #0e0e0f;
    --card-edge: #1b1b1c;
    --gold: #d9b24a;
    --gold-soft: #b8953a;
    --grey: #959595;
    --white: #f4f4f4;
  }
  * { margin: 0; padding: 0; box-sizing: border-box; }
  html, body {
    width: 1200px; height: 864px; overflow: hidden;
    background: var(--backdrop);
  }
  .stage {
    position: relative; width: 1200px; height: 864px;
    display: flex; align-items: center; justify-content: center; gap: 60px;
  }
  .card {
    position: relative; width: 520px; height: 297px;
    background: var(--card-black);
    border: 1px solid var(--card-edge);
    box-shadow: 0 18px 40px rgba(0,0,0,.45);
  }
  /* front */
  .card-front {
    display: flex; flex-direction: column; align-items: center; justify-content: center;
  }
  .brand-dot {
    width: 64px; height: 64px; border-radius: 50%;
    background: var(--gold); margin-bottom: 18px;
  }
  .brand-name {
    font-family: "Cinzel", serif; font-weight: 600;
    color: var(--gold); text-align: center; line-height: 1;
  }
  .brand-name .word { display: block; font-size: 46px; letter-spacing: 1px; }
  .brand-name .place { display: block; font-size: 14px; letter-spacing: 4px; margin-top: 8px; }
  .site {
    margin-top: 26px;
    font-family: "PT Sans", sans-serif; font-size: 15px;
    letter-spacing: 5px; color: var(--grey);
  }
  /* back */
  .card-back { display: flex; align-items: center; }
  .holder {
    width: 262px; padding-right: 18px; text-align: right;
  }
  .holder-name {
    font-family: "Cinzel", serif; font-weight: 600; font-size: 19px;
    color: var(--gold); letter-spacing: .5px;
  }
  .holder-role {
    margin-top: 4px;
    font-family: "PT Sans", sans-serif; font-size: 15px; color: var(--white);
  }
  .divider {
    width: 1px; height: 108px; background: var(--grey); opacity: .7;
  }
  .contacts {
    list-style: none; padding-left: 18px;
    font-family: "PT Sans", sans-serif; font-size: 13.5px; color: var(--white);
  }
  .contacts li { display: flex; align-items: center; height: 19px; }
  .contacts .icon { width: 11px; height: 11px; margin-right: 7px; fill: var(--gold); }
  .contacts .plain { padding-left: 0; }
</style>
</head>
<body>
<main class="stage">
  <section class="card card-front" aria-label="Card front">
    <span class="brand-dot"></span>
    <h1 class="brand-name"><span class="word">LORVANTI</span><span class="place">ITALY</span></h1>
    <p class="site">www.lorvanti.com</p>
  </section>

  <section class="card card-back" aria-label="Card back">
    <div class="holder">
      <h2 class="holder-name">Dario Lorvanti</h2>
      <p class="holder-role">CEO &amp; CO Founder</p>
    </div>
    <span class="divider"></span>
    <ul class="contacts">
      <li class="plain">4817 E Halvern</li>
      <li><svg class="icon" viewBox="0 0 12 12"><path d="M2.5 0.8 4.4 0.8 5.2 3.4 3.9 4.4C4.6 5.9 6 7.3 7.6 8L8.6 6.8 11.2 7.6 11.2 9.5C11.2 10.4 10.4 11.2 9.5 11.2 4.7 11 1 7.3.8 2.5.8 1.6 1.6.8 2.5.8Z"/></svg>555-384-1926</li>
      <li><svg class="icon" viewBox="0 0 12 12"><path d="M3 0.8h5v3H3z M1 4.5h10v6.5H1z" /><rect x="3" y="6.5" width="6" height="1" fill="#0e0e0f"/><rect x="3" y="8.5" width="6" height="1" fill="#0e0e0f"/></svg>555-384-1926</li>
      <li><svg class="icon" viewBox="0 0 12 12"><path d="M0.8 2.2h10.4v7.6H0.8z"/><path d="M1 2.6 6 6.6 11 2.6" fill="none" stroke="#0e0e0f" stroke-width="1"/></svg>dario@lorvanti.com</li>
      <li><svg class="icon" viewBox="0 0 12 12"><path d="M6 .5C3.8.5 2.2 2.1 2.2 4.2 2.2 7 6 11.5 6 11.5S9.8 7 9.8 4.2C9.8 2.1 8.2.5 6 .5Z"/><circle cx="6" cy="4.2" r="1.4" fill="#0e0e0f"/></svg>LORVANTI.COM</li>
    </ul>
  </section>
</main>
</body>
</html>
```